Ferncliff Capital - Website Design

We need a website design for a new commercial real estate company called Ferncliff Capital. We're effectively commercial mortgage brokers connecting real estate investors to lenders. We need a website that is simple (not busy), elegant, professional, and user-friendly. A lot of the users will be in their 50's and less tech savvy, so a stream-lined design is best. The website will serve as a portal for lenders to review new financing opportunities, as well as for real estate investors to review terms from lenders.
Updates
Just uploaded our logo.
Target Market(s)
Commercial real estate investors and lenders
Industry/Entity Type
Real Estate
Number of Pages Required
1 page
Colors
Designer to choose colors to be used in the design.
Look and feel

```html
<!DOCTYPE html>
<html lang="en">
<head>
<meta charset="utf-8">
<title>Ferncliff Capital</title>
<link rel="stylesheet" href="https://fonts.googleapis.com/css2?family=Open+Sans:wght@400;600;700&display=swap">
<style>
:root{
  --brand:#3551d8;
  --brand-dark:#2a44c8;
  --ink:#444a55;
  --muted:#666c78;
  --white:#ffffff;
  --card:#ececec;
  --footer:#1f2a4e;
  --footer-text:#aab2cc;
}
*{margin:0;padding:0;box-sizing:border-box}
html,body{width:1200px;height:2571px;overflow:hidden}
body{font-family:"Open Sans",Arial,sans-serif;background:var(--white);color:var(--ink);position:relative}

.site-header{position:absolute;top:0;left:0;width:1200px;height:79px;background:var(--brand)}
.brand-block{position:absolute;left:0;top:0;width:600px;height:79px;background:var(--brand-dark)}
.brand-name{position:absolute;left:129px;top:17px;font-size:37px;font-weight:600;color:var(--white);letter-spacing:-0.2px}
.main-nav{position:absolute;top:29px;left:686px;display:flex;gap:0}
.main-nav a{font-size:13.5px;color:#d6ddff;text-decoration:none;text-transform:uppercase;margin-right:33px}
.main-nav a.is-active{color:var(--white);text-decoration:underline;text-underline-offset:3px}

.hero{position:absolute;top:79px;left:0;width:1200px;height:533px;background:linear-gradient(100deg,#e9eef2 0%,#c9d6e0 35%,#3d4f6a 45%,#5b6f8c 60%,#b7d9e6 75%,#e6f3f5 100%)}
.hero-arrow{position:absolute;top:253px;width:28px;height:28px;border-radius:50%;background:rgba(120,120,120,.75)}
.hero-arrow svg{display:block}
.hero-arrow.prev{left:32px}
.hero-arrow.next{left:1140px}

.welcome{position:absolute;top:612px;left:0;width:1200px;height:274px;text-align:center}
.section-title{font-size:24px;font-weight:700;color:var(--brand);text-transform:uppercase}
.welcome .section-title{margin-top:75px}
.welcome p{width:930px;margin:12px auto 0;font-size:11.3px;line-height:21px;color:var(--muted)}

.services{position:absolute;top:886px;left:0;width:1200px;height:437px;background:var(--brand);color:var(--white)}
.services .section-title{color:var(--white);text-align:center;margin-top:73px}
.service{position:absolute;top:137px;width:290px}
.service:nth-of-type(1){left:132px}
.service:nth-of-type(2){left:456px}
.service:nth-of-type(3){left:780px}
.service-icon{height:62px}
.service h3{margin-top:13px;font-size:19px;font-weight:400}
.service p{margin-top:8px;font-size:10.3px;line-height:18px;color:#dfe4ff}
.btn{display:inline-block;width:96px;height:40px;line-height:38px;text-align:center;font-size:10.5px;text-decoration:none}
.btn-light{margin-top:15px;border:1px solid var(--white);color:var(--white)}

.feature{position:absolute;top:1323px;left:0;width:1200px;height:400px;background:linear-gradient(180deg,#9fb0c0 0%,#e8c79a 35%,#7a6a55 60%,#6c7b3e 80%,#8c8d6a 100%)}
.play{position:absolute;left:574px;top:173px;width:50px;height:50px}

.projects{position:absolute;top:1723px;left:0;width:1200px;height:728px}
.projects .section-title{text-align:center;margin-top:70px}
.project{position:absolute;top:135px;width:440px;height:513px;background:var(--card)}
.project:nth-of-type(1){left:132px}
.project:nth-of-type(2){left:627px}
.project-photo{height:257px}
.project:nth-of-type(1) .project-photo{background:linear-gradient(135deg,#5d8fd1 0%,#b8cde6 40%,#e9edf0 70%,#8e9aa6 100%)}
.project:nth-of-type(2) .project-photo{background:linear-gradient(180deg,#1b46c9 0%,#3a6fe0 40%,#4b5d7a 75%,#c98d3a 100%)}
.project-body{padding:22px 22px 0}
.project h3{font-size:17.5px;font-weight:400;line-height:24px;color:#333}
.project p{margin-top:12px;font-size:10.3px;line-height:17.5px;color:var(--muted)}
.btn-outline{margin-top:20px;border:1px solid #aaa;color:#777;width:98px}

.site-footer{position:absolute;top:2451px;left:0;width:1200px;height:120px;background:var(--footer)}
.footer-nav{position:absolute;left:132px;top:34px;font-size:12.5px;color:var(--footer-text)}
.footer-nav a{color:var(--footer-text);text-decoration:none}
.footer-nav span{margin:0 9px}
.copyright{position:absolute;left:132px;top:63px;font-size:12.5px;color:var(--footer-text)}
.social{position:absolute;left:1010px;top:46px;display:flex;gap:6px}
.social span{display:block;width:24px;height:24px;border-radius:50%}
.social .social-a{background:#3b5fb0}
.social .social-b{background:#2aa3e0}
</style>
</head>
<body>

<header class="site-header">
  <div class="brand-block"><div class="brand-name">Ferncliff Capital</div></div>
  <nav class="main-nav">
    <a href="#" class="is-active">Home</a>
    <a href="#">About</a>
    <a href="#">Services</a>
    <a href="#">Projects</a>
    <a href="#">Contact Us</a>
  </nav>
</header>

<section class="hero" role="img" aria-label="Businessman in a suit holding a city skyline in his open hand against a blue sky">
  <span class="hero-arrow prev"><svg width="28" height="28" viewBox="0 0 28 28"><path d="M16 8 L10 14 L16 20" fill="none" stroke="#fff" stroke-width="2.5"/></svg></span>
  <span class="hero-arrow next"><svg width="28" height="28" viewBox="0 0 28 28"><path d="M12 8 L18 14 L12 20" fill="none" stroke="#fff" stroke-width="2.5"/></svg></span>
</section>

<section class="welcome">
  <h2 class="section-title">Welcome to Ferncliff Capital</h2>
  <p>Fusce sollicitudin lorem et luctus volutpat. Proin placerat dapibus gravida. In tristique tristique nulla eget hendrerit. Maecenas vel tortor accumsan quam varius imperdiet vel eget elit. Aenean facilisis tincidunt lectus, id dictum nisl luctus eget. Vivamus efficitur ex condimentum, malesuada eros eget, feugiat nibh. Sed tellus ex, imperdiet eget gravida sit amet, volutpat eget turpis. In nec ultricies est. Etiam mattis augue vehicula odio posuere, sit amet tempus lectus luctus. Nulla facilisi. Etiam vel massa elementum, bibendum tellus venenatis, feugiat massa. Curabitur venenatis lacinia ornare.</p>
</section>

<section class="services">
  <h2 class="section-title">What We Do</h2>
  <div class="service">
    <svg class="service-icon" width="66" height="62" viewBox="0 0 66 62" fill="none" stroke="#fff" stroke-width="2">
      <path d="M4 30 L33 4 L62 30"/><path d="M12 23 V58 H54 V23"/><rect x="27" y="28" width="13" height="13"/><path d="M33.5 28 V41 M27 34.5 H40"/>
    </svg>
    <h3>Nullam urna</h3>
    <p>Suspendisse gravida ornare erat sed pulvinar. Vestibulum luctus ex in egestas fringilla. Fusce nec leo ac urna pulvinar auctor. Mauris bibendum fringilla velit.</p>
    <a href="#" class="btn btn-light">Read more</a>
  </div>
  <div class="service">
    <svg class="service-icon" width="92" height="62" viewBox="0 0 92 62" fill="none" stroke="#fff" stroke-width="2" stroke-linejoin="round">
      <path d="M2 18 L18 8 L30 28 L14 38 Z"/><path d="M90 18 L74 8 L62 28 L78 38 Z"/>
      <path d="M26 22 L40 16 L52 18 L64 26"/><path d="M30 28 L44 44 Q48 48 52 44 L66 30"/>
      <path d="M44 24 L56 36 M40 30 L52 42 M36 34 L46 46"/>
    </svg>
    <h3>Nulla tristique</h3>
    <p>Suspendisse gravida ornare erat sed pulvinar. Vestibulum luctus ex in egestas fringilla. Fusce nec leo ac urna pulvinar auctor. Mauris bibendum fringilla velit.</p>
    <a href="#" class="btn btn-light">Read more</a>
  </div>
  <div class="service">
    <svg class="service-icon" width="92" height="62" viewBox="0 0 92 62" fill="none" stroke="#fff" stroke-width="2">
      <circle cx="18" cy="16" r="8"/><circle cx="46" cy="12" r="9"/><circle cx="74" cy="16" r="8"/>
      <path d="M4 60 V38 Q4 28 18 28 Q32 28 32 38 V60"/><path d="M32 60 V34 Q32 24 46 24 Q60 24 60 34 V60"/><path d="M60 60 V38 Q60 28 74 28 Q88 28 88 38 V60"/>
    </svg>
    <h3>Aliquam erat</h3>
    <p>Suspendisse gravida ornare erat sed pulvinar. Vestibulum luctus ex in egestas fringilla. Fusce nec leo ac urna pulvinar auctor. Mauris bibendum fringilla velit.</p>
    <a href="#" class="btn btn-light">Read more</a>
  </div>
</section>

<section class="feature" role="img" aria-label="Modern apartment buildings with green landscaping at sunset, video preview">
  <svg class="play" viewBox="0 0 50 50"><circle cx="25" cy="25" r="24" fill="#fff"/><circle cx="25" cy="25" r="19" fill="none" stroke="#222" stroke-width="2"/><path d="M20 16 L34 25 L20 34 Z" fill="#222"/></svg>
</section>

<section class="projects">
  <h2 class="section-title">Projects</h2>
  <article class="project">
    <div class="project-photo" role="img" aria-label="White modern apartment building with balconies under a blue sky"></div>
    <div class="project-body">
      <h3>Cras eget leo sed nunc hendrerit ultricies eu at nisl. Praesent iaculis faucibus urna sit amet lacinia.</h3>
      <p>Maecenas consequat justo enim, ac mattis massa imperdiet quis. Fusce eget neque elit. Sed augue orci, elementum in magna congue, tincidunt vulputate erat. Aliquam consectetur orci molestie dictum molestie. Proin eget congue nulla, vel tempor diam. Fusce sollicitudin lorem et luctus volutpat.</p>
      <a href="#" class="btn btn-outline">Read more</a>
    </div>
  </article>
  <article class="project">
    <div class="project-photo" role="img" aria-label="Glass residential towers lit up at dusk"></div>
    <div class="project-body">
      <h3>Cras eget leo sed nunc hendrerit ultricies eu at nisl. Praesent iaculis faucibus urna sit amet lacinia.</h3>
      <p>Maecenas consequat justo enim, ac mattis massa imperdiet quis. Fusce eget neque elit. Sed augue orci, elementum in magna congue, tincidunt vulputate erat. Aliquam consectetur orci molestie dictum molestie. Proin eget congue nulla, vel tempor diam. Fusce sollicitudin lorem et luctus volutpat.</p>
      <a href="#" class="btn btn-outline">Read more</a>
    </div>
  </article>
</section>

<footer class="site-footer">
  <nav class="footer-nav">
    <a href="#">Home</a><span>|</span><a href="#">About</a><span>|</span><a href="#">Services</a><span>|</span><a href="#">Projects</a><span>|</span><a href="#">Contact Us</a>
  </nav>
  <div class="copyright">Copyright &copy; 2017 &nbsp;Ferncliff Capital. &nbsp;All rights reserved.</div>
  <div class="social">
    <span class="social-a" aria-label="Social link"></span>
    <span class="social-b" aria-label="Social link"></span>
  </div>
</footer>

</body>
</html>
```